Stonebrace Business Card Design

The Stonebrace Co is an aggregate (crushing) equipment dealer serving Western Canadian provinces. Stonebrace is a distributor of aggregate equipment for different manufacturers.

We are looking to change and update the existing business card which has been used since the existence of the company. A copy of existing card has been attached for reference. The Stonebrace Co logo we want to remain the same and we want the green color to remain the same.

We are wanting something new with a different look. A refreshing card to show a new modern and updated look. No longer wanting to have the manufacturers on the back of the card but something more like our logo on the back of the card with a statement like "Crushing Solutions"

ideas could be:
- card can be different colors on front and back
- front or reverse of the card could possibly be the green color with the logo in black

Target Market(s)

Owners of Aggregate/Crushing companies

Contact Information for Business Card

see above

Requirements
Must have
• - logo to remain same along with same font within logo
• - green color to remain same
Nice to have
• as noted above under project description
Should not have

```html
<!DOCTYPE html>
<html lang="en">
<head>
<meta charset="utf-8">
<title>The Stonebrace Co – Business Card</title>
<link href="https://fonts.googleapis.com/css2?family=Roboto:wght@400;500;700&family=Roboto+Condensed:wght@700&display=swap" rel="stylesheet">
<style>
  :root {
    --backdrop: #5a4838;
    --card-white: #f3f3f3;
    --brand-green: #8a8c05;
    --ink: #231f20;
    --text-grey: #4a4a4a;
    --rule-grey: #8a8a8a;
  }
  html, body {
    margin: 0;
    width: 1200px;
    height: 960px;
    overflow: hidden;
    background: var(--backdrop);
    font-family: "Roboto", Arial, sans-serif;
  }
  .canvas { position: relative; width: 1200px; height: 960px; }
  .card {
    position: absolute;
    width: 600px;
    height: 343px;
    border-radius: 18px;
    overflow: hidden;
  }
  .card--front { left: 314px; top: 113px; background: var(--card-white); }
  .card--back { left: 311px; top: 472px; background: var(--brand-green); }

  .wordmark {
    position: absolute;
    display: flex;
    align-items: center;
    gap: 12px;
    font-weight: 700;
    color: var(--ink);
    white-space: nowrap;
  }
  .wordmark__dot { border-radius: 50%; flex: none; }
  .card--front .wordmark { left: 44px; top: 56px; font-size: 18px; }
  .card--front .wordmark__dot { width: 26px; height: 26px; background: var(--brand-green); }

  .person__name {
    position: absolute; left: 41px; top: 172px; margin: 0;
    font-family: "Roboto Condensed", "Arial Narrow", sans-serif;
    font-weight: 700; font-size: 21px; color: var(--brand-green); letter-spacing: .2px;
  }
  .person__role {
    position: absolute; left: 41px; top: 198px; width: 510px;
    display: flex; align-items: center; gap: 8px;
    font-weight: 500; font-size: 14px; color: var(--ink);
  }
  .person__role::after {
    content: ""; flex: 1; border-bottom: 1px dotted var(--rule-grey); margin-top: 2px;
  }

  .contact { position: absolute; font-size: 14px; color: var(--text-grey); line-height: 19px; }
  .contact--phones { left: 44px; top: 228px; }
  .contact__line { display: flex; align-items: center; gap: 7px; }
  .contact__line svg { width: 13px; height: 13px; fill: var(--brand-green); flex: none; }
  .contact__divider {
    position: absolute; left: 176px; top: 252px; width: 1px; height: 30px; background: var(--brand-green);
  }
  .contact--web { left: 191px; top: 246px; }
  .contact--address { left: 42px; top: 294px; }

  .card--back .wordmark {
    left: 0; right: 0; top: 126px; flex-direction: column; gap: 34px;
    font-size: 23px; color: var(--ink);
  }
  .card--back .wordmark__dot { width: 72px; height: 72px; background: var(--ink); }
  .tagline {
    position: absolute; left: 0; right: 0; top: 291px; margin: 0;
    text-align: center; font-weight: 700; font-size: 15px; color: var(--ink);
  }
</style>
</head>
<body>
<main class="canvas">
  <section class="card card--front" aria-label="Card front">
    <div class="wordmark"><span class="wordmark__dot"></span><span>THE STONEBRACE CO.</span></div>

    <h1 class="person__name">DALE MORVEN</h1>
    <div class="person__role">CEO/FOUNDER</div>

    <div class="contact contact--phones">
      <div class="contact__line">
        <svg viewBox="0 0 16 16" aria-label="Phone"><path d="M3.5 1 6 1.2 7 4.8 5.3 6.1a9 9 0 0 0 4.6 4.6L11.2 9l3.6 1 .2 2.5c0 1-1 2-2 2C6.6 14.5 1.5 9.4 1.5 3c0-1 1-2 2-2z"/></svg>
        <span>780.555.0142</span>
      </div>
      <div class="contact__line">
        <svg viewBox="0 0 16 16" aria-label="Mobile"><path d="M4 0h8a1 1 0 0 1 1 1v14a1 1 0 0 1-1 1H4a1 1 0 0 1-1-1V1a1 1 0 0 1 1-1zm1 2v10h6V2zm3 11a1 1 0 1 0 0 2 1 1 0 0 0 0-2z"/></svg>
        <span>780.555.0187</span>
      </div>
      <div class="contact__line">
        <svg viewBox="0 0 16 16" aria-label="Fax"><path d="M4 1h7l1 1v4H4zM1 7h14v6H1zm3 3v5h8v-5z"/></svg>
        <span>780.555.0163</span>
      </div>
    </div>
    <div class="contact__divider"></div>
    <div class="contact contact--web">
      <div>dale@stonebr.com</div>
      <div>www.stonebrace.ca</div>
    </div>
    <div class="contact contact--address">2218- 48B Street, Camrose, Alberta T4V 1K9</div>
  </section>

  <section class="card card--back" aria-label="Card back">
    <div class="wordmark"><span class="wordmark__dot"></span><span>THE STONEBRACE CO.</span></div>
    <p class="tagline">Crushing Solutions</p>
  </section>
</main>
</body>
</html>
```